Medical Billing Company Needs a Business Card Design

We need a business card design for a Florida based medical billing company called 'Clinicians Keystone Solutions'. We specialize in providing revenue cycle management services to physician and therapist offices (we're basically their back-office processing partner for providing billing software, claims submissions, A/R follow-up and patient statements & collections. Our logo is red and blue-ish, so make sure that whatever other elements are used will match appropriately. Our current business card design has a too small font size. I'd like to project an image that shows we are modern & reliable. On a side note, I'm planning on using ZUB for printing these cards.

Target Market(s)

Office managers, physicians, therapists

Industry/Entity Type

Printing

Requirements
Must have
• Logo
Name of Employee
Phone
Fax
E-mail
Website

```html
<!DOCTYPE html>
<html lang="en">
<head>
<meta charset="utf-8">
<title>Clinicians Keystone Solutions – Business Card</title>
<link rel="stylesheet" href="https://fonts.googleapis.com/css2?family=Open+Sans:wght@400;600;700&display=swap">
<style>
  :root {
    --bg: #e9e9ee;
    --card: #ffffff;
    --navy: #2e2a7a;
    --purple: #3c2a8c;
    --purple-light: #5a4aa6;
    --red: #b3202a;
    --ink: #3a3a3f;
    --white: #ffffff;
  }
  * { margin: 0; padding: 0; box-sizing: border-box; }
  html, body { width: 1200px; height: 987px; overflow: hidden; }
  body {
    background: var(--bg);
    font-family: "Open Sans", Arial, sans-serif;
    position: relative;
  }
  .card {
    position: absolute;
    left: 215px;
    width: 770px;
    height: 440px;
    background: var(--card);
    border-radius: 34px;
    overflow: hidden;
    box-shadow: 0 6px 18px rgba(0,0,0,0.12);
  }
  .card--front { top: 32px; }
  .card--back { top: 515px; }

  .wave { position: absolute; inset: 0; width: 100%; height: 100%; }

  .brand-name {
    position: absolute;
    font-weight: 400;
    color: var(--navy);
    letter-spacing: 3px;
    text-transform: uppercase;
    white-space: nowrap;
    display: flex;
    align-items: center;
    gap: 14px;
  }
  .brand-name__mark {
    width: 22px; height: 22px;
    background: var(--red);
  }
  .card--front .brand-name { left: 250px; top: 52px; font-size: 38px; }

  .holder {
    position: absolute;
    left: 88px; top: 120px;
    font-size: 24px;
    font-weight: 700;
    color: var(--purple-light);
  }
  .holder__title { font-weight: 400; color: var(--red); font-size: 21px; }

  .contacts {
    position: absolute;
    left: 70px; top: 166px;
    list-style: none;
    font-size: 18px;
    color: var(--ink);
    line-height: 24px;
  }
  .contacts li { display: flex; align-items: center; gap: 8px; }
  .contacts svg { width: 15px; height: 15px; flex: none; }

  .address {
    position: absolute;
    right: 40px; bottom: 30px;
    text-align: right;
    color: var(--white);
    font-size: 23px;
    line-height: 32px;
  }

  .card--back .brand-name {
    left: 50%; top: 150px;
    transform: translateX(-50%);
    font-size: 46px;
  }
  .website {
    position: absolute;
    left: 0; right: 0; top: 245px;
    text-align: center;
    font-size: 22px;
    letter-spacing: 6px;
    color: var(--ink);
  }
</style>
</head>
<body>

<section class="card card--front" aria-label="Business card front">
  <svg class="wave" viewBox="0 0 770 440" preserveAspectRatio="none" aria-hidden="true">
    <defs>
      <linearGradient id="waveFill" x1="0" y1="0" x2="1" y2="1">
        <stop offset="0" stop-color="#5c4aa8"/>
        <stop offset="1" stop-color="#2a1a78"/>
      </linearGradient>
    </defs>
    <path d="M0,215 C50,310 250,325 470,318 C620,313 720,318 770,338 L770,440 L0,440 Z" fill="url(#waveFill)"/>
    <path d="M22,250 C80,330 270,345 480,338 C630,334 720,340 770,358" fill="none" stroke="#ffffff" stroke-width="5" stroke-linecap="round"/>
  </svg>

  <div class="brand-name"><span class="brand-name__mark"></span>Clinicians Keystone</div>

  <p class="holder">Your Name, <span class="holder__title">Title</span></p>

  <ul class="contacts">
    <li>
      <svg viewBox="0 0 16 16" aria-hidden="true"><circle cx="8" cy="8" r="7.5" fill="#3c2a8c"/><path d="M5 4.5l1.6-.3.8 2-1 .8a6 6 0 0 0 2.6 2.6l.8-1 2 .8-.3 1.6c-3.5.2-6.7-3-6.5-6.5z" fill="#fff"/></svg>
      123-456-0789
    </li>
    <li>
      <svg viewBox="0 0 16 16" aria-hidden="true"><rect x="4" y="1" width="8" height="14" rx="1.5" fill="#3c2a8c"/><rect x="5.5" y="3" width="5" height="7" fill="#fff"/></svg>
      123-456-0789
    </li>
    <li>
      <svg viewBox="0 0 16 16" aria-hidden="true"><circle cx="8" cy="8" r="7.5" fill="#3c2a8c"/><rect x="4" y="5" width="8" height="6" fill="#fff"/><path d="M4 5l4 3.2L12 5" fill="none" stroke="#3c2a8c" stroke-width="1"/></svg>
      info@clinicianskeystone.com
    </li>
    <li>
      <svg viewBox="0 0 16 16" aria-hidden="true"><circle cx="8" cy="8" r="7.5" fill="#3c2a8c"/><circle cx="8" cy="8" r="5" fill="none" stroke="#fff" stroke-width="1"/><path d="M3 8h10M8 3v10" stroke="#fff" stroke-width="1"/></svg>
      www.clinicianskeystone.com
    </li>
  </ul>

  <address class="address">Street Name, City Name<br>State Zip Code</address>
</section>

<section class="card card--back" aria-label="Business card back">
  <div class="brand-name"><span class="brand-name__mark"></span>Clinicians Keystone</div>
  <p class="website">www.clinicianskeystone.com</p>
</section>

</body>
</html>
```